my website is tavorinque.com. (brand name is ta belle vitrine) This is just a template that i have choose for. The content and the pictures are not about my business just the template.
I would like to have 4 pages for now. 1 homepage, which will be an overview for all pages, it is right now in this way. It will directly highlight my story. My website will tell an exclusive story about details which makes the difference and will make people happy with very small things. It will be art related but very stylish as well. I also want to have a event agenda on my homepage where people can see where my next event is. Page 2 my blog, where I will write weekly about mindset, lifestyle and details. Inspiration place for people who are looking for unique and exclusive approaches in life. Page 3 shop, where I will sell my stuff which is handmade and unique, it will be limited edition stuff. Mostly I will make the designs from marbling art, which I am a teacher for. (https://www.vidoranta.com/watch?v=KpwuzRaxTmo) check this video out for more. Page 4 is book page. Here people will be able to book private or group classes for marbling art (check the video). I have already a community of more than 500 people on gath rix, which will be my public as well. I wanna implement the gath rix button on this page as well. to be able to track.

This is about my website. I also need a logo for my brand, which will suit my website and my goals.

I can also give you a reference website, which really like as structure and style;
https://www.brightorvalco.com/products/the-morning-ledger?gclid=Xr4TpLmwq2HsVD9KEBsZTrc-WkPhyQ-uvlEjdRs3NKaOYFCBWMpuTzG8xyCVbhdnLWRqoaNf_2e8ZtpRvHbAwq9FLQ_hqgQ

Logo Text

ta belle vitrine

Coding

Coded - Design and coding required

Number of Pages Required

4 page

Requirements
Must have
• I can also give you a reference website, which really like as structure and style;
• https://www.brightorvalco.com/products/the-morning-ledger?gclid=Xr4TpLmwq2HsVD9KEBsZTrc-WkPhyQ-uvlEjdRs3NKaOYFCBWMpuTzG8xyCVbhdnLWRqoaNf_2e8ZtpRvHbAwq9FLQ_hqgQ

```html
<!DOCTYPE html>
<html lang="en">
<head>
<meta charset="utf-8">
<title>ta belle vitrine</title>
<link rel="stylesheet" href="https://fonts.googleapis.com/css2?family=Kaushan+Script&family=Open+Sans:wght@400;600&family=Noto+Serif:wght@400;700&display=swap">
<style>
:root{
  --ink:#333;
  --muted:#777;
  --line:#e6e6e6;
  --soft:#f5f5f5;
  --accent:#e59a2e;
  --btn:#3a3a3a;
  --btn-grey:#6b6b6b;
  --pink:#e9c8c9;
  --blush:#f2d6d6;
  --footer:#2b2b2b;
  --white:#fff;
}
*{box-sizing:border-box;margin:0;padding:0}
html,body{width:1200px;height:3766px;overflow:hidden}
body{position:relative;background:var(--white);font-family:"Open Sans",Arial,sans-serif;color:var(--ink)}
.abs{position:absolute}
.script{font-family:"Kaushan Script",cursive;font-weight:400}
.serif{font-family:"Noto Serif",Georgia,serif}
.center{text-align:center}

/* nav */
.nav{left:0;top:0;width:1200px;height:100px;background:var(--white)}
.nav a{position:absolute;top:42px;font-size:13px;color:var(--ink);text-decoration:none;letter-spacing:.5px}
.brand{left:0;width:1200px;top:34px;text-align:center;font-family:"Noto Serif",Georgia,serif;font-size:20px;color:var(--ink)}

/* hero */
.hero{left:0;top:100px;width:1200px;height:515px;background:linear-gradient(120deg,#5a4a3a 0%,#7a5a7a 25%,#a07890 45%,#6a4a68 65%,#8a7a5a 85%,#4a3a3a 100%)}
.hero-box{left:251px;top:251px;width:708px;height:276px;background:rgba(40,35,35,.45)}
.hero-title{left:0;top:268px;width:1200px;font-size:72px;color:var(--white)}
.hero-text{left:270px;top:380px;width:660px;font-family:"Noto Serif",Georgia,serif;font-size:13px;line-height:30px;color:var(--white)}
.btn-pink{left:527px;top:452px;width:146px;height:40px;background:var(--blush);color:var(--ink);font-size:13px;line-height:40px;text-align:center}
.arrow{width:52px;height:52px;border:2px solid var(--white);border-radius:50%;top:328px}

/* section titles */
.sec-title{left:0;width:1200px;font-size:44px;color:var(--ink)}
.sec-sub{left:0;width:1200px;font-size:11px;color:var(--muted)}

/* products */
.card{top:771px;width:239px;height:371px;border:1px solid var(--line);background:var(--white)}
.card .photo{position:absolute;left:12px;top:12px;width:215px;height:196px}
.card .price{position:absolute;left:0;top:230px;width:100%;text-align:center;font-family:"Noto Serif",Georgia,serif;font-weight:700;font-size:26px;color:var(--accent)}
.card .name{position:absolute;left:0;top:270px;width:100%;text-align:center;font-family:"Noto Serif",Georgia,serif;font-size:21px;color:#555}
.card .icons{position:absolute;left:67px;top:313px}

/* story */
.story{left:0;top:1205px;width:1200px;height:1275px;background:var(--soft)}
.round{border-radius:50%;border:8px solid var(--white);box-shadow:0 2px 8px rgba(0,0,0,.18)}
.st-head{font-size:26px;color:var(--ink)}
.st-text{font-size:11px;line-height:28px;color:#555;width:500px}
.btn-dark{height:44px;line-height:44px;background:var(--btn);color:var(--white);font-size:13px;text-align:center}

/* events */
.post{width:300px;text-align:center}
.post h3{font-family:"Noto Serif",Georgia,serif;font-weight:400;font-size:15px;color:var(--ink)}
.post .date{font-family:"Noto Serif",Georgia,serif;font-size:13px;color:#555;margin-top:8px}
.post p{font-size:12px;line-height:28px;color:#555;margin-top:6px}
.btn-grey{height:45px;line-height:45px;width:148px;background:var(--btn-grey);color:var(--white);font-family:"Noto Serif",Georgia,serif;font-size:14px;text-align:center}

/* subscribe */
.subscribe{left:0;top:3238px;width:1200px;height:289px;background:linear-gradient(135deg,#e6c2c3,#eed3d3 50%,#e4bfc0)}
.input{left:233px;top:3404px;width:595px;height:47px;background:var(--white);font-size:11px;color:#666;padding-left:18px;line-height:47px}
.submit{left:828px;top:3404px;width:138px;height:47px;background:#555;color:var(--white);font-size:12px;text-align:center;line-height:47px}

/* footer */
.footer{left:0;top:3527px;width:1200px;height:239px;background:var(--footer)}
.social{top:3560px;width:60px;height:60px;border:1px solid #888;border-radius:50%}
.foot-link{top:3658px;font-size:12px;color:#ddd;letter-spacing:.5px}
.copy{left:0;width:1200px;top:3700px;font-size:11px;color:#ccc;text-align:center}
</style>
</head>
<body>

<header class="abs nav">
  <a style="left:108px">HOME</a>
  <a style="left:220px">BLOG</a>
  <a style="left:322px">SHOP</a>
  <a style="left:426px">BOOK</a>
  <div class="abs brand">ta belle vitrine</div>
  <svg class="abs" style="left:838px;top:43px" width="14" height="14" viewBox="0 0 14 14"><path d="M1 2h2l2 8h7l1.5-6H4" fill="none" stroke="#333" stroke-width="1.4"/><circle cx="6" cy="12.5" r="1" fill="#333"/><circle cx="11" cy="12.5" r="1" fill="#333"/></svg>
  <a style="left:860px;font-size:11px;top:43px">$0.00 ▾</a>
  <svg class="abs" style="left:945px;top:42px" width="14" height="14" viewBox="0 0 14 14"><circle cx="6" cy="6" r="4.5" fill="none" stroke="#333" stroke-width="1.5"/><path d="M9.5 9.5L13 13" stroke="#333" stroke-width="1.6"/></svg>
  <a style="left:968px;font-size:11px;top:43px">SEARCH</a>
  <svg class="abs" style="left:1056px;top:43px" width="12" height="13" viewBox="0 0 12 13"><circle cx="6" cy="4" r="3" fill="#333"/><path d="M0 13c0-4 3-5 6-5s6 1 6 5z" fill="#333"/></svg>
  <a style="left:1072px;font-size:11px;top:43px">LOGIN</a>
</header>

<section>
  <div class="abs hero" role="img" aria-label="Marbling art paint swirls in purple, ochre and green"></div>
  <div class="abs hero-box"></div>
  <h1 class="abs hero-title script center">ta belle vitrine</h1>
  <p class="abs hero-text center">ta belle vitrine is a trendsetting Online Store, offering our first-rate products and exceptional customer service to shoppers from the comfort of their own homes. We're a business made up of marblers</p>
  <div class="abs btn-pink">SHOP NOW</div>
  <svg class="abs arrow" style="left:24px" viewBox="0 0 52 52"><path d="M29 18l-8 8 8 8" fill="none" stroke="#fff" stroke-width="2.5"/></svg>
  <svg class="abs arrow" style="left:1122px" viewBox="0 0 52 52"><path d="M23 18l8 8-8 8" fill="none" stroke="#fff" stroke-width="2.5"/></svg>
</section>

<section>
  <h2 class="abs sec-title script center" style="top:642px">Our Products</h2>
  <p class="abs sec-sub center" style="top:720px">ta belle vitrine is a trendsetting Online Store, offering our first-rate products and exceptional customer service to shoppers.</p>

  <div class="abs card" style="left:88px">
    <div class="photo" role="img" aria-label="Marbled fabric with pink and green floral swirls" style="background:linear-gradient(135deg,#6a9a8a,#b8d0c0 40%,#d86a7a 65%,#5a7a5a)"></div>
    <div class="price">€85.00</div><div class="name">I'M A PRODUCT</div>
    <svg class="icons" width="105" height="30" viewBox="0 0 105 30"><g fill="none" stroke="#aaa"><circle cx="15" cy="15" r="13"/><circle cx="52" cy="15" r="13"/><circle cx="89" cy="15" r="13"/><path d="M9 10h2l2 7h5l1-5h-7"/><path d="M52 20l-5-5a3 3 0 015-3 3 3 0 015 3z"/><rect x="84" y="11" width="10" height="8"/></g></svg>
  </div>
  <div class="abs card" style="left:346px">
    <div class="photo" role="img" aria-label="Marbling tray with brown and white paint pattern" style="background:linear-gradient(135deg,#3a3030,#8a5a4a 40%,#c8a898 60%,#7a4a3a)"></div>
    <div class="price">€20.00</div><div class="name">I'M A PRODUCT</div>
    <svg class="icons" width="105" height="30" viewBox="0 0 105 30"><g fill="none" stroke="#aaa"><circle cx="15" cy="15" r="13"/><circle cx="52" cy="15" r="13"/><circle cx="89" cy="15" r="13"/><path d="M9 10h2l2 7h5l1-5h-7"/><path d="M52 20l-5-5a3 3 0 015-3 3 3 0 015 3z"/><rect x="84" y="11" width="10" height="8"/></g></svg>
  </div>
  <div class="abs card" style="left:607px">
    <div class="photo" role="img" aria-label="Comb drawing through pink marbling paint" style="background:linear-gradient(135deg,#8a5a5a,#c89090 45%,#e0b0a8 60%,#7a4a4a)"></div>
    <div class="price">€10.00</div><div class="name">I'M A PRODUCT</div>
    <svg class="icons" width="105" height="30" viewBox="0 0 105 30"><g fill="none" stroke="#aaa"><circle cx="15" cy="15" r="13"/><circle cx="52" cy="15" r="13"/><circle cx="89" cy="15" r="13"/><path d="M9 10h2l2 7h5l1-5h-7"/><path d="M52 20l-5-5a3 3 0 015-3 3 3 0 015 3z"/><rect x="84" y="11" width="10" height="8"/></g></svg>
  </div>
  <div class="abs card" style="left:868px">
    <div class="photo" role="img" aria-label="Dark marbling tray with colour bottles" style="background:linear-gradient(180deg,#5a3a4a,#2a2a2a 40%,#1a1a1a 70%,#4a4a4a)"></div>
    <div class="price">€25.00</div><div class="name">I'M A PRODUCT</div>
    <svg class="icons" width="105" height="30" viewBox="0 0 105 30"><g fill="none" stroke="#aaa"><circle cx="15" cy="15" r="13"/><circle cx="52" cy="15" r="13"/><circle cx="89" cy="15" r="13"/><path d="M9 10h2l2 7h5l1-5h-7"/><path d="M52 20l-5-5a3 3 0 015-3 3 3 0 015 3z"/><rect x="84" y="11" width="10" height="8"/></g></svg>
  </div>
</section>

<section>
  <div class="abs story"></div>
  <svg class="abs" style="left:0;top:1205px" width="1200" height="1275" viewBox="0 0 1200 1275">
    <g fill="none" stroke="#999" stroke-width="1.5" stroke-dasharray="5 5">
      <path d="M299 351V432H878V497"/>
      <path d="M878 793V863H299V930"/>
    </g>
    <circle cx="299" cy="351" r="9" fill="#777"/>
    <circle cx="878" cy="793" r="9" fill="#777"/>
  </svg>

  <div class="abs round" role="img" aria-label="Marbling tray with new pattern" style="left:156px;top:1270px;width:286px;height:286px;background:linear-gradient(160deg,#3a3a3a,#8a5a4a 40%,#c8a898 55%,#7a4a3a)"></div>
  <h3 class="abs st-head script" style="left:540px;top:1286px">Our New Arrivals Are Here</h3>
  <p class="abs st-text" style="left:540px;top:1342px">ta belle vitrine is a leading Online Store. We provide an unparalleled selection of the very best quality products, an easy and comfortable shopping experience, expedited shipping offers, &amp; exceptional customer service. Check out our collection of new arrivals, best-sellers,&amp; provide an unparalleled selection of the clearance items today.</p>
  <div class="abs btn-dark" style="left:540px;top:1481px;width:140px">SHOP NOW!</div>

  <h3 class="abs st-head script" style="left:148px;top:1722px">Origins</h3>
  <p class="abs st-text" style="left:148px;top:1781px">ta belle vitrine is a leading Online Store. We provide an unparalleled selection of the very best quality products, an easy and comfortable shopping experience, expedited shipping offers, &amp; exceptional customer service. Check out our collection of new arrivals, best-sellers,&amp; provide an unparalleled selection of the clearance items today.</p>
  <div class="abs btn-dark" style="left:148px;top:1921px;width:146px">SHOP NOW!</div>
  <div class="abs round" role="img" aria-label="Purple marbling pattern with round cells" style="left:735px;top:1707px;width:286px;height:286px;background:radial-gradient(circle at 40% 40%,#d8c0d8,#8a5a8a 50%,#4a3a4a)"></div>

  <div class="abs round" role="img" aria-label="Marbling workshop tray with colour bottles" style="left:156px;top:2139px;width:286px;height:286px;background:linear-gradient(180deg,#6a4a5a,#3a3a3a 40%,#1a1a1a 70%,#5a5a5a)"></div>
  <h3 class="abs st-head script" style="left:540px;top:2160px">Book Online</h3>
  <p class="abs st-text" style="left:540px;top:2212px">ta belle vitrine is a leading Online Store. We provide an unparalleled selection of the very best quality products, an easy and comfortable shopping experience, expedited shipping offers, &amp; exceptional customer service. Check out our collection of new arrivals, best-sellers,&amp; provide an unparalleled selection of the clearance items today.</p>
  <div class="abs btn-dark" style="left:540px;top:2353px;width:140px">SHOP NOW!</div>
</section>

<section>
  <h2 class="abs sec-title script center" style="top:2504px">Latest Events</h2>
  <p class="abs sec-sub center" style="top:2577px">ta belle vitrine is a trendsetting Online Store, offering our first-rate products and exceptional customer service to shoppers</p>

  <article class="abs post" style="left:164px;top:2650px">
    <h3>THIS IS YOUR FIRST POST</h3>
    <div class="date">Date : May 9, 2016</div>
    <p>This is your blog post. Blogs are a great way to connect with your audience and keep them coming great way tauthority in your field.</p>
  </article>
  <div class="abs round" role="img" aria-label="Comb drawing through pink marbling" style="left:214px;top:2812px;width:200px;height:200px;background:radial-gradient(circle,#e0b0a8,#a06060 60%,#6a3a3a)"></div>
  <div class="abs btn-grey" style="left:183px;top:3030px">READ MORE</div>

  <article class="abs post" style="left:452px;top:2748px">
    <h3>THIS IS YOUR SECOND POST</h3>
    <div class="date">Date : May 9, 2016</div>
    <p>This is your blog post. Blogs are a great way to connect with your audience and keep them coming great way tauthority in your field.</p>
  </article>
  <div class="abs round" role="img" aria-label="Dark marbling tray with colour rings" style="left:502px;top:2902px;width:200px;height:200px;background:radial-gradient(circle,#4a4a4a,#1a1a1a 70%)"></div>
  <div class="abs btn-grey" style="left:528px;top:3131px">READ MORE</div>

  <article class="abs post" style="left:796px;top:2650px">
    <h3>THIS IS YOUR THIRD POST</h3>
    <div class="date">Date : May 9, 2016</div>
    <p>This is your blog post. Blogs are a great way to connect with your audience and keep them coming great way tauthority in your field.</p>
  </article>
  <div class="abs round" role="img" aria-label="Marbled fabric with floral swirls" style="left:846px;top:2812px;width:200px;height:200px;background:radial-gradient(circle,#b8d0c0,#d86a7a 50%,#5a7a5a)"></div>
  <div class="abs btn-grey" style="left:873px;top:3030px">READ MORE</div>
</section>

<section>
  <div class="abs subscribe"></div>
  <h2 class="abs sec-title script center" style="top:3268px;font-size:32px;color:var(--white)">Subscribe Stay up to date</h2>
  <p class="abs sec-sub center" style="top:3338px;color:var(--white)">ta belle vitrine is a trendsetting Online Store, offering our first-rate products and exceptional customer service to shoppers.</p>
  <div class="abs input">Enter Your Email</div>
  <div class="abs submit">SUBMIT</div>
</section>

<footer>
  <div class="abs footer"></div>
  <div class="abs social" style="left:392px" aria-label="Social link"></div>
  <div class="abs social" style="left:462px" aria-label="Social link"></div>
  <div class="abs social" style="left:532px" aria-label="Social link"></div>
  <div class="abs social" style="left:603px" aria-label="Social link"></div>
  <div class="abs social" style="left:675px" aria-label="Social link"></div>
  <svg class="abs social" style="left:746px" viewBox="0 0 60 60" aria-label="Email"><rect x="22" y="24" width="16" height="12" fill="none" stroke="#fff" stroke-width="1.5"/><path d="M22 24l8 7 8-7" fill="none" stroke="#fff" stroke-width="1.5"/></svg>
  <div class="abs" style="left:90px;top:3635px;width:1020px;height:1px;background:#444"></div>
  <span class="abs foot-link" style="left:380px">HOME</span>
  <span class="abs foot-link" style="left:462px;color:#888">|</span>
  <span class="abs foot-link" style="left:516px">BLOG</span>
  <span class="abs foot-link" style="left:598px;color:#888">|</span>
  <span class="abs foot-link" style="left:652px">SHOP</span>
  <span class="abs foot-link" style="left:732px;color:#888">|</span>
  <span class="abs foot-link" style="left:784px">BOOK</span>
  <p class="abs copy">© Copyrights 2017 ta belle vitrine.All. Rights Reserved.</p>
</footer>

</body>
</html>
```